Internet Service Tech provider product flyer redesign - High Rise WIFI

We have created the attached flyer in Word and also attached a PDF. All the content is correct. We just need a complete re-design of the flyer with new relevant hi-res images (based on content) and a more streamlined/cleaner layout.

This product is an entire in-building WIFI system for Body's Corporate in High Rise buildings.

We are a Brisbane-based internet tech company that specialises in providing solutions for High Rise buildings

Body text style - Helvetica Light

Internet

```html
<!DOCTYPE html>
<html lang="en">
<head>
<meta charset="utf-8">
<title>High Rise WiFi – Our Technologies</title>
<link rel="stylesheet" href="https://fonts.googleapis.com/css2?family=Archivo+Black&family=Oswald:wght@500;600&family=Roboto:wght@300;400&display=swap">
<style>
  :root {
    --ink: #1b1f22;
    --band: #0b2329;
    --accent-blue: #1f80d2;
    --stripe: #2c6878;
    --white: #ffffff;
    --orb-light: #4a8fd6;
    --orb-mid: #2566b0;
    --orb-dark: #123c7c;
    --contact: #dfe8ec;
    --sky-light: #c4d8ea;
    --sky: #8fb2d3;
    --tower: #4f5f72;
    --tower-dark: #2c3540;
    --suit: #1a1c20;
  }
  html, body { margin: 0; padding: 0; overflow: hidden; background: #ffffff; }
  .flyer {
    position: relative;
    width: 848px;
    height: 1200px;
    overflow: hidden;
    background: var(--white);
    font-family: "Roboto", "Helvetica Neue", Arial, sans-serif;
    color: var(--ink);
  }
  .hero-photo {
    position: absolute;
    left: 0;
    top: 0;
    width: 460px;
    height: 1200px;
    background:
      radial-gradient(ellipse 180px 420px at 250px 330px, rgba(60,76,96,0.85) 0%, rgba(60,76,96,0) 100%),
      radial-gradient(ellipse 260px 320px at 150px 900px, rgba(26,28,32,0.9) 0%, rgba(26,28,32,0) 100%),
      linear-gradient(180deg, var(--sky-light) 0%, var(--sky) 30%, var(--tower) 52%, var(--tower-dark) 72%, var(--suit) 100%);
  }
  .frame-shapes { position: absolute; inset: 0; }
  .contact {
    position: absolute;
    left: 497px;
    top: 30px;
  }
  .contact-title {
    margin: 0 0 10px;
    font-family: "Oswald", "Arial Narrow", sans-serif;
    font-weight: 600;
    font-size: 29px;
    letter-spacing: 0.3px;
    color: var(--accent-blue);
  }
  .contact-line {
    margin: 0;
    font-size: 16px;
    line-height: 22px;
    font-weight: 400;
    color: var(--contact);
  }
  .section-title {
    position: absolute;
    left: 502px;
    top: 284px;
    margin: 0;
    font-family: "Archivo Black", "Arial Black", sans-serif;
    font-size: 25px;
    font-weight: 400;
    color: var(--band);
  }
  .orb {
    position: absolute;
    width: 156px;
    height: 156px;
    border-radius: 50%;
    background: radial-gradient(circle at 50% 25%, var(--orb-light) 0%, var(--orb-mid) 50%, var(--orb-dark) 100%);
    box-shadow: 0 0 0 9px var(--white);
    display: flex;
    align-items: center;
    justify-content: center;
    text-align: center;
    font-family: "Oswald", "Arial Narrow", sans-serif;
    font-weight: 500;
    font-size: 24px;
    line-height: 36px;
    color: var(--white);
    letter-spacing: 0.5px;
  }
  .orb--bulk { left: 312px; top: 360px; }
  .orb--wifi { left: 262px; top: 642px; }
  .orb--billing { left: 150px; top: 896px; }
  .feature-list { margin: 0; padding: 0; list-style: none; }
  .feature-list li {
    position: absolute;
    font-size: 15.5px;
    font-weight: 300;
    line-height: 20px;
    white-space: nowrap;
    color: var(--ink);
  }
</style>
</head>
<body>
<main class="flyer">
  <div class="hero-photo" role="img" aria-label="High-resolution photo of a businessman in a suit working on a laptop, with a glass high-rise office tower rising behind him against a blue sky"></div>

  <svg class="frame-shapes" width="848" height="1200" viewBox="0 0 848 1200" aria-hidden="true">
    <path d="M30 0 Q150 62 372 92" fill="none" stroke="var(--white)" stroke-width="9"/>
    <path d="M364 0 C402 250 382 520 312 760 S162 1130 97 1200 L848 1200 L848 0 Z" fill="var(--white)"/>
    <path d="M364 0 C402 250 382 520 312 760 S162 1130 97 1200" fill="none" stroke="var(--white)" stroke-width="30"/>
    <path d="M364 0 C402 250 382 520 312 760 S162 1130 97 1200" fill="none" stroke="var(--stripe)" stroke-width="14"/>
    <path d="M396 0 L848 0 L848 148 Q640 196 412 172 Q404 80 396 0 Z" fill="var(--band)"/>
  </svg>

  <section class="contact">
    <h2 class="contact-title">GET IN TOUCH</h2>
    <p class="contact-line">info@skyriseconnect.com.au</p>
    <p class="contact-line">www.skyriseconnect.com.au</p>
  </section>

  <h1 class="section-title">Our Technologies</h1>

  <div class="orb orb--bulk">BULK<br>SUPPLY</div>
  <ul class="feature-list">
    <li style="left:497px;top:366px">Licensed telecommunications and internet</li>
    <li style="left:497px;top:384px">service carrier</li>
    <li style="left:496px;top:410px">Technology designed for multiresident usage</li>
    <li style="left:494px;top:435px">Corporate backup connections included</li>
    <li style="left:492px;top:460px">Up to 1000Mbps speed downloads/uploads</li>
    <li style="left:491px;top:487px">1000Mbps embedded network infrastructure</li>
    <li style="left:487px;top:512px">Professional service guaranteed</li>
    <li style="left:484px;top:538px">99.999% uptime service level agreements</li>
  </ul>

  <div class="orb orb--wifi">HD WIFI</div>
  <ul class="feature-list">
    <li style="left:469px;top:639px">High definition output up to 30+dBm</li>
    <li style="left:466px;top:664px">Multi-radio design</li>
    <li style="left:462px;top:691px">10/100/1000 Ethernet LAN connection</li>
    <li style="left:456px;top:716px">Up to 300Mbps data transfer rates – per radio</li>
    <li style="left:450px;top:742px">LED signal strength display</li>
    <li style="left:443px;top:768px">SNMP remote management and configuration</li>
    <li style="left:437px;top:793px">Stealth design to blend into building aesthetics</li>
  </ul>

  <div class="orb orb--billing">AUTOMATED<br>BILLING</div>
  <ul class="feature-list">
    <li style="left:391px;top:920px">Tier 1 PCS-DSS certified</li>
    <li style="left:384px;top:945px">Branded web portal for payment gateway</li>
    <li style="left:373px;top:972px">Fast payment processing</li>
    <li style="left:361px;top:997px">SSL security for payment transactions</li>
    <li style="left:349px;top:1023px">Local, friendly, and professional support</li>
    <li style="left:336px;top:1048px">Guest self service and payment</li>
    <li style="left:324px;top:1075px">Get paid 24/7</li>
  </ul>
</main>
</body>
</html>
```